Webdesign für Honigmanufaktur
Zielgruppe
Imkerei, Verkauf von Honig und Honigerzeugnissen, so wie Bienenwachskerzen.
Zielgruppe sind vermutlich Frauen im mittleren bis gehobenen Alter.
Aufgabenstellung
Es gibt ein Firmenlogo.
Ich bevorzuge als Grundfarbe weiß, lasse mich aber von guten Einfällen gerne überraschen.
Die Website www.kelvaroni.at finde ich sehr ansprechend.
Nur ohne Musik.
Ohne Deutsch/Englisch Auswahl.
Es soll danach Word press verwendet werden.

```html
<!DOCTYPE html>
<html lang="de">
<head>
<meta charset="utf-8">
<title>Imkerei Lindenhain – Der Shop</title>
<link href="https://fonts.googleapis.com/css2?family=Lato:wght@300;400&family=Roboto+Condensed:wght@400;700&family=Roboto:ital,wght@0,400;0,500;0,700;1,400&display=swap" rel="stylesheet">
<style>
:root{
  --stage:#f1f1f1;
  --page:#ffffff;
  --ink:#2b2b2b;
  --muted:#8a8a8a;
  --line:#e6e6e6;
  --honey:#f29a1f;
  --honey-dark:#6b3a12;
  --link:#1aa3e8;
  --tile:#ececec;
}
*{margin:0;padding:0;box-sizing:border-box}
html,body{width:683px;height:1200px;overflow:hidden;background:var(--stage)}
body{position:relative;font-family:"Roboto",sans-serif;color:var(--ink)}
.page{position:absolute;left:32px;top:32px;width:619px;height:1133px;background:var(--page)}

/* header */
.header{position:absolute;left:0;top:0;width:619px;height:52px;border-bottom:1px solid var(--line)}
.account-links{position:absolute;left:414px;top:3px;width:84px;font-family:"Roboto Condensed",sans-serif;font-size:3.6px;letter-spacing:.5px;color:var(--muted);display:flex;gap:8px;border-bottom:1px solid var(--line);padding-bottom:3px;justify-content:flex-end}
.brand{position:absolute;left:247px;top:3px;width:120px;text-align:center}
.brand-mark{width:24px;height:24px;margin:0 auto;border-radius:50%;border:2.5px solid var(--honey)}
.brand-name{font-family:"Roboto Condensed",sans-serif;font-weight:700;font-size:7px;color:var(--honey-dark);letter-spacing:.3px;margin-top:7px}
.brand-sub{font-family:"Roboto Condensed",sans-serif;font-size:4px;color:var(--honey);letter-spacing:2px}
.nav a{position:absolute;top:37px;transform:translateX(-50%);font-family:"Roboto Condensed",sans-serif;font-size:4.2px;letter-spacing:.9px;color:#555;text-decoration:none;white-space:nowrap}
.nav a.active{color:var(--honey)}
.nav a.active::before,.nav a.active::after{content:"";position:absolute;left:2px;right:2px;height:3px;border:1px solid var(--ink)}
.nav a.active::before{top:-4px;border-bottom:none}
.nav a.active::after{bottom:-4px;border-top:none}

.banner{position:absolute;left:113px;top:65px;width:387px;height:54px;background:linear-gradient(90deg,#5c6a4e 0%,#8d86b5 25%,#4b5a3c 45%,#7d72ae 70%,#56623f 100%)}

/* sidebar */
.sidebar{position:absolute;left:118px;top:135px;width:120px}
.sidebar h3{font-weight:400;font-size:4.5px;letter-spacing:.3px;display:flex;align-items:center;gap:6px}
.sidebar h3::after{content:"";flex:1;height:1px;background:var(--line)}
.sidebar ul{list-style:none;margin-top:4px}
.sidebar li{font-size:4.2px;height:11.6px;line-height:11.6px;padding-left:6.5px;position:relative}
.sidebar li.open::before{content:"›";position:absolute;left:1px;font-size:5px}

/* products */
.product{position:absolute;width:87px;text-align:center}
.product-photo{width:87px;height:87px;background:radial-gradient(ellipse 22px 28px at 50% 50%,var(--honey) 0%,#f0b55a 55%,var(--tile) 100%)}
.product-photo.caramel{background:radial-gradient(ellipse 22px 28px at 50% 50%,#b45d1f 0%,#d48a4a 55%,var(--tile) 100%)}
.product-photo.vanilla{background:radial-gradient(ellipse 22px 28px at 50% 50%,#f2c93c 0%,#f3dc8b 55%,var(--tile) 100%)}
.product-name{font-size:4.6px;margin-top:8px;height:14px}
.stars{font-size:4.5px;color:#aaa;letter-spacing:.3px;margin-top:2px}
.price{font-size:6px;color:var(--honey);margin-top:1px}
.base-price{font-size:3.2px;margin-top:2px}
.tax{font-size:3.2px;margin-top:3px}
.tax span{color:var(--link)}
.cart-btn{display:block;margin:4px auto 0;width:59px;height:11px;line-height:10px;border:1px solid var(--honey);font-size:3.8px;font-style:italic;font-weight:500}

/* newsletter */
.newsletter{position:absolute;left:118px;top:670px;width:387px;height:97px;background:linear-gradient(180deg,#f3f3f3,#e6e6e6)}
.newsletter h2{position:absolute;top:30px;width:100%;text-align:center;font-family:"Lato",sans-serif;font-weight:300;font-size:9.5px;letter-spacing:.6px;color:#333}
.nl-input{position:absolute;left:105px;top:49px;width:110px;height:14px;background:#fff;border:1px solid #ddd;font-size:3.8px;color:var(--muted);line-height:12px;padding-left:6px}
.nl-btn{position:absolute;left:217px;top:49px;width:58px;height:14px;background:var(--honey);color:#fff;font-size:3.8px;letter-spacing:.8px;line-height:14px;text-align:center}

/* intro text */
.intro-title{position:absolute;left:113px;top:786px;width:387px;text-align:center;font-family:"Lato",sans-serif;font-weight:300;font-size:9.5px;letter-spacing:.9px;color:#333}
.intro{position:absolute;left:150px;width:319px}
.intro h4{font-size:4.1px;font-weight:500;line-height:7px}
.intro p{font-size:4.1px;color:var(--muted);line-height:7.1px}

/* footer */
.footer-rule{position:absolute;left:113px;top:939px;width:387px;height:1px;background:var(--honey)}
.fcol{position:absolute;top:953px;width:95px}
.fcol h5{font-size:4.5px;font-weight:500;margin-bottom:9px}
.fcol li{list-style:none;font-size:3.9px;color:var(--muted);line-height:7.7px}
.fcol p{font-size:3.9px;color:var(--muted);line-height:7.7px}
.fcol p b{color:var(--ink);font-weight:400}
.social{display:flex;gap:6px;margin-top:9px}
.social i{width:5px;height:5px;border-radius:50%;background:#666;display:block}
.bottom-rule{position:absolute;left:0;top:1062px;width:619px;height:1px;background:var(--line)}
.copyright{position:absolute;top:1075px;width:619px;text-align:center;font-size:3.8px;color:var(--muted)}
.payments{position:absolute;top:1086px;left:255px;display:flex;gap:4.5px}
.payments span{width:17px;height:10px;border:1px solid var(--line);font-size:3.4px;line-height:8px;text-align:center;color:#555;font-weight:500}
</style>
</head>
<body>
<div class="page">
  <header class="header">
    <div class="account-links"><span>MEIN KONTO</span><span>WARENKORB (0)</span></div>
    <div class="brand">
      <div class="brand-mark"></div>
      <div class="brand-name">IMKEREI LINDENHAIN</div>
      <div class="brand-sub">HONIG &amp; WACHS</div>
    </div>
    <nav class="nav">
      <a style="left:146px">STARTSEITE</a>
      <a style="left:198px">DIE MANUFAKTUR</a>
      <a style="left:249px">DER HONIG</a>
      <a style="left:373px">DAS BIENENWACHS</a>
      <a class="active" style="left:429px">DER SHOP</a>
      <a style="left:475px">KONTAKT</a>
    </nav>
  </header>

  <div class="banner" role="img" aria-label="Biene auf blühendem Lavendel"></div>

  <aside class="sidebar">
    <h3>KATEGORIEN</h3>
    <ul>
      <li class="open">Honigspezialitäten (11)</li>
      <li>Bienenwachskerzen (3)</li>
      <li>Honigwein (5)</li>
      <li>Geschenkideen (12)</li>
    </ul>
  </aside>

  <div class="product" style="left:215px;top:136px"><div class="product-photo" role="img" aria-label="Honigglas Orange"></div><div class="product-name">Honig mit Orange</div><div class="stars">★★★★★</div><div class="price">€5,95</div><div class="base-price">Grundpreis: €5,95 /100g</div><div class="tax">Inkl. Mwst.; zzgl. <span>Versandkosten</span></div><span class="cart-btn">In den Warenkorb legen</span></div>
  <div class="product" style="left:312px;top:136px"><div class="product-photo caramel" role="img" aria-label="Honigglas Karamell"></div><div class="product-name">Honig mit Karamell</div><div class="stars">★★★★★</div><div class="price">€5,95</div><div class="base-price">Grundpreis: €5,95 /100g</div><div class="tax">Inkl. Mwst.; zzgl. <span>Versandkosten</span></div><span class="cart-btn">In den Warenkorb legen</span></div>
  <div class="product" style="left:408px;top:136px"><div class="product-photo vanilla" role="img" aria-label="Honigglas Vanille"></div><div class="product-name">Honig mit Vanille</div><div class="stars">★★★★★</div><div class="price">€5,95</div><div class="base-price">Grundpreis: €5,95 /100g</div><div class="tax">Inkl. Mwst.; zzgl. <span>Versandkosten</span></div><span class="cart-btn">In den Warenkorb legen</span></div>

  <div class="product" style="left:215px;top:306px"><div class="product-photo vanilla" role="img" aria-label="Honigglas Vanille"></div><div class="product-name">Honig mit Vanille</div><div class="stars">★★★★★</div><div class="price">€5,95</div><div class="base-price">Grundpreis: €5,95 /100g</div><div class="tax">Inkl. Mwst.; zzgl. <span>Versandkosten</span></div><span class="cart-btn">In den Warenkorb legen</span></div>
  <div class="product" style="left:312px;top:306px"><div class="product-photo" role="img" aria-label="Honigglas Orange"></div><div class="product-name">Honig mit Orange</div><div class="stars">★★★★★</div><div class="price">€5,95</div><div class="base-price">Grundpreis: €5,95 /100g</div><div class="tax">Inkl. Mwst.; zzgl. <span>Versandkosten</span></div><span class="cart-btn">In den Warenkorb legen</span></div>
  <div class="product" style="left:408px;top:306px"><div class="product-photo vanilla" role="img" aria-label="Honigglas Vanille"></div><div class="product-name">Honig mit Vanille</div><div class="stars">★★★★★</div><div class="price">€5,95</div><div class="base-price">Grundpreis: €5,95 /100g</div><div class="tax">Inkl. Mwst.; zzgl. <span>Versandkosten</span></div><span class="cart-btn">In den Warenkorb legen</span></div>

  <div class="product" style="left:215px;top:475px"><div class="product-photo" role="img" aria-label="Honigglas Orange"></div><div class="product-name">Honig mit Orange</div><div class="stars">★★★★★</div><div class="price">€5,95</div><div class="base-price">Grundpreis: €5,95 /100g</div><div class="tax">Inkl. Mwst.; zzgl. <span>Versandkosten</span></div><span class="cart-btn">In den Warenkorb legen</span></div>
  <div class="product" style="left:312px;top:475px"><div class="product-photo vanilla" role="img" aria-label="Honigglas Vanille"></div><div class="product-name">Honig mit Vanille</div><div class="stars">★★★★★</div><div class="price">€5,95</div><div class="base-price">Grundpreis: €5,95 /100g</div><div class="tax">Inkl. Mwst.; zzgl. <span>Versandkosten</span></div><span class="cart-btn">In den Warenkorb legen</span></div>
  <div class="product" style="left:408px;top:475px"><div class="product-photo caramel" role="img" aria-label="Honigglas Karamell"></div><div class="product-name">Honig mit Karamell</div><div class="stars">★★★★★</div><div class="price">€5,95</div><div class="base-price">Grundpreis: €5,95 /100g</div><div class="tax">Inkl. Mwst.; zzgl. <span>Versandkosten</span></div><span class="cart-btn">In den Warenkorb legen</span></div>

  <section class="newsletter" role="img" aria-label="Heller, verschwommener Hintergrund mit Bienen">
    <h2>JETZT FÜR UNSEREN AKTUELLEN NEWSLETTER ANMELDEN</h2>
    <div class="nl-input">E-Mail Adresse hier eingeben ...</div>
    <div class="nl-btn">ABSENDEN</div>
  </section>

  <h2 class="intro-title">EXKLUSIVER HONIG AUS DEM PFÄLZERWALD</h2>
  <div class="intro" style="top:818px">
    <h4>Lorem ipsum dolor sit amet, consetetur sadipscing elitr, sed diam nonumy eirmod tempor invidunt</h4>
    <p>Lorem ipsum dolor sit amet, consetetur sadipscing elitr, sed diam nonumy eirmod tempor invidunt ut labore et dolore magna aliquyam erat, sed diam voluptua. At vero eos et accusam et justo duo dolores et ea rebum. Stet clita kasd gubergren, no sea takimata sanctus est Lorem ipsum dolor sit amet. Lorem ipsum dolor sit amet, consetetur sadipscing elitr, sed diam nonumy eirmod tempor invidunt ut labore et dolore magna aliquyam erat, sed diam voluptua. At vero eos et accusam et justo duo dolores et ea rebum. Stet clita kasd gubergren, no sea takimata sanctus est Lorem ipsum dolor sit amet. Lorem ipsum dolor sit amet, consetetur sadipscing elitr, sed diam nonumy eirmod tempor invidunt ut labore.</p>
  </div>
  <div class="intro" style="top:867px">
    <h4>Lorem ipsum dolor sit amet, consetetur sadipscing elitr, sed diam nonumy eirmod tempor invidunt</h4>
    <p>Lorem ipsum dolor sit amet, consetetur sadipscing elitr, sed diam nonumy eirmod tempor invidunt ut labore et dolore magna aliquyam erat, sed diam voluptua. At vero eos et accusam et justo duo dolores et ea rebum. Stet clita kasd gubergren, no sea takimata sanctus est Lorem ipsum dolor sit amet. Lorem ipsum dolor sit amet, consetetur sadipscing elitr, sed diam nonumy eirmod tempor invidunt ut labore et dolore magna aliquyam erat, sed diam voluptua. At vero eos et accusam et justo duo dolores et ea rebum. Stet clita kasd gubergren, no sea takimata sanctus est Lorem ipsum dolor sit amet. Lorem ipsum dolor sit amet, consetetur sadipscing elitr, sed diam nonumy eirmod tempor invidunt ut labore et</p>
  </div>

  <div class="footer-rule"></div>
  <div class="fcol" style="left:118px">
    <h5>Imkerei Lindenhain © 2018</h5>
    <p>Lorem ipsum dolor sit amet, consetetur sadipscing elitr, sed diam nonumy eirmod tempor invidunt ut labore et dolore magna aliquyam erat, sed diam voluptua. Lorem ipsum dolor sit amet, consetetur sadipscing</p>
    <p style="margin-top:4px"><b>Telefon:</b> 0000 000 0000<br><b>E-Mail:</b> service@lindenhain-honig.de</p>
    <div class="social"><i></i><i></i><i></i><i></i><i></i></div>
  </div>
  <div class="fcol" style="left:215px">
    <h5>Unternehmen</h5>
    <ul><li>Die Manufaktur</li><li>Der Honig</li><li>Das Bienenwachs</li><li>Kontaktformular</li><li>Datenschutz</li><li>Impressum</li></ul>
  </div>
  <div class="fcol" style="left:312px">
    <h5>Service</h5>
    <ul><li>FAQ</li><li>Lieferung &amp; Versand</li><li>AGB</li><li>Widerrufsbelehrung</li><li>Widerrufsformular</li><li>Glossar</li><li>Kundenmeinungen</li></ul>
  </div>
  <div class="fcol" style="left:408px">
    <h5>Mein Konto</h5>
    <ul><li>Kundenkonto anlegen</li><li>Meine Bestellungen</li><li>Meine Nachrichten</li><li>Mein Wunschzettel</li><li>Produkte vergleichen</li></ul>
  </div>

  <div class="bottom-rule"></div>
  <div class="copyright">Copyright © 2018 Imkerei Lindenhain | Musterstraße 10 | 12345 Musterstadt | Tel. 012 345 678 | Fax 012 345 678 | info@lindenhain-honig.de</div>
  <div class="payments"><span>Orvel</span><span>Tannik</span><span>Brisa</span><span>Holmex</span><span>Quenta</span></div>
</div>
</body>
</html>
```